Verdel Harvest - Stationery Design Project

We need a stationary for our business. We grow roots and fruits in Central and South America, we import and distribute in FL, USA. We do fresh and frozen products.

Target Market(s)

Small and big supermarkets, wholesalers, traders, distributors, etc

Industry/Entity Type

Business

```html
<!DOCTYPE html>
<html lang="en">
<head>
<meta charset="utf-8">
<title>Verdel Harvest – Stationery</title>
<link rel="stylesheet" href="https://fonts.googleapis.com/css2?family=Questrial&display=swap">
<style>
  :root {
    --backdrop-light: #f1f3f4;
    --backdrop-dark: #d9e0e4;
    --paper: #ffffff;
    --paper-back: #f1f1f1;
    --brand-orange: #e8800a;
    --brand-green: #4d6330;
    --rule-grey: #555555;
    --ink: #3a3a3a;
    --ink-soft: #222222;
  }
  * { box-sizing: border-box; margin: 0; padding: 0; }
  html, body { width: 1200px; height: 927px; overflow: hidden; }
  body {
    position: relative;
    font-family: "Questrial", "Century Gothic", sans-serif;
    background: radial-gradient(ellipse at 50% 40%, var(--backdrop-light) 0%, var(--backdrop-dark) 100%);
    color: var(--ink);
  }
  .sheet {
    position: absolute;
    top: 45px;
    width: 512px;
    height: 696px;
    border-radius: 12px;
    box-shadow: 0 1px 4px rgba(0,0,0,.25);
    overflow: hidden;
  }
  .sheet--front { left: 43px; background: var(--paper); }
  .sheet--back { left: 635px; background: var(--paper-back); }

  .brand {
    position: absolute;
    left: 0; right: 0;
    display: flex;
    justify-content: center;
    align-items: center;
    gap: 8px;
    color: var(--brand-orange);
    letter-spacing: 1px;
    text-transform: uppercase;
    white-space: nowrap;
  }
  .brand__dot { width: 14px; height: 14px; border-radius: 50%; background: var(--brand-green); }
  .sheet--front .brand { top: 40px; font-size: 26px; }
  .sheet--back .brand { top: 598px; font-size: 30px; }

  .header-rule {
    position: absolute; left: 40px; right: 40px; top: 99px;
    height: 3px; background: var(--rule-grey);
  }
  .contact-line {
    position: absolute; left: 40px; right: 40px; top: 102px;
    display: flex; justify-content: space-between;
    font-size: 11px; font-weight: bold; color: var(--brand-orange);
  }
  .letter-body {
    position: absolute; left: 44px; top: 142px; width: 425px;
    font-size: 10.6px; line-height: 17.7px; text-align: justify; color: var(--ink);
  }
  .letter-body p + p { margin-top: 17.7px; }
  .signature {
    position: absolute; left: 379px; top: 582px; color: var(--ink-soft);
  }
  .signature__name { font-size: 14px; }
  .signature__title { font-size: 10px; margin-top: 8px; }

  .footer-rule {
    position: absolute; left: 0; right: 0; top: 660px; height: 5px; background: var(--brand-green);
  }
  .footer-band {
    position: absolute; left: 0; right: 0; top: 665px; bottom: 0;
    background: var(--brand-orange);
    display: flex; justify-content: space-between; align-items: center;
    padding: 0 40px 0 26px;
    font-size: 10px; font-weight: bold; color: var(--ink-soft);
  }

  .deliverables {
    position: absolute; left: 34px; top: 804px;
    list-style: none;
    font-size: 25px; line-height: 34px; color: #111;
    text-transform: uppercase; letter-spacing: .3px;
  }
  .deliverables li::before { content: "- "; }
</style>
</head>
<body>
  <section class="sheet sheet--front" aria-label="Letterhead">
    <div class="brand"><span class="brand__dot"></span><span>Verdel Harvest</span></div>
    <div class="header-rule"></div>
    <div class="contact-line">
      <span>info@verdelharvest.com</span>
      <span>www.verdelharvest.com</span>
    </div>
    <div class="letter-body">
      <p>Lorem ipsum dolor sit amet, consectetur adipiscing elit. Donec orci purus, luctus vitae dignissim eu, iaculis sed purus. Vivamus faucibus, ipsum nec aliquet viverra, leo mauris condimentum ligula, sit amet sagittis enim ligula quis arcu. Nam egestas tortor id nisi porttitor mattis. In tortor ante, ultricies in suscipit a, tempus non massa. Vivamus et auctor mi. Fusce vel massa nulla. Phasellus nec eros mauris, et scelerisque orci. Donec malesuada orci vitae nulla accumsan porta a id massa.</p>
      <p>Quisque accumsan iaculis magna sit amet fringilla. Maecenas consequat, magna eget tincidunt semper, odio nibh rutrum mi, id feugiat ante nisi eu risus. Vestibulum nunc orci, rhoncus a placerat in, ultricies in mi. Cras mattis varius eros, vel fringilla nisi suscipit eget. Quisque scelerisque sagittis nulla at porttitor. Mauris a justo et tellus interdum tristique. Sed id augue vitae urna euismod commodo aliquet a quam. Pellentesque arcu velit, cursus et malesuada ut, consequat et diam. Nullam erat sem, rhoncus id ullamcorper vitae, rhoncus et arcu. In ultricies ultricies nulla.</p>
      <p>Kut rutrum nisi iaculis at. Donec eu magna a metus ornare faucibus. Fusce aliquet faucibus ultricies. Morbi semper, est id tincidunt gravida, sem arcu adipiscing lacus, ac bibendum nulla leo eu purus. Quisque nec diam sed risus consectetur a ccumsan quis quis nibh. Vestibulum id purus lorem. Donec eu magna a metus ornare faucibus. Fusce aliquet faucibus ultricies. Morbi semper, est id tincidunt gravida, sem arcu adipiscing lacus, ac bibendum nulla leo eu purus. Quisque nec diam sed risus consectetur a ccumsan quis quis nibh. Vestibulum id purus lorem.</p>
    </div>
    <div class="signature">
      <div class="signature__name">Tomas Reyna</div>
      <div class="signature__title">Co-Founder &amp; CEO</div>
    </div>
    <div class="footer-rule"></div>
    <div class="footer-band">
      <span>Ph: 305.410.2286</span>
      <span>Fax: 305.410.2290</span>
      <span>Toll Free: 855.410.2200</span>
    </div>
  </section>

  <section class="sheet sheet--back" aria-label="Letterhead reverse">
    <div class="brand"><span class="brand__dot"></span><span>Verdel Harvest</span></div>
  </section>

  <ul class="deliverables">
    <li>Print ready &amp; editable files</li>
    <li>PSD, JPG, TIFF, PNG, AI, EPS file formats</li>
    <li>Unlimited revisions are most welcome</li>
  </ul>
</body>
</html>
```